Business Card for Vorla Parts Wholesale supplier

Hi There! I need a new business card for our company. We are specialized in selling Vorla parts, mostly we sell new LCD screens for Zelnar and Drelks. I would like to see that back in the design.

You can find the colors and logo's on our website: www.hartuvo.nl

Industry/Entity Type

Business

Contact Information for Business Card

My Details:
Tobias Lindqvist

Phone: 0031687203316
E-mail: Tobias@hartuvo.nl

Slogan: "Because Quality Matters"

Font styles to use
Sans Serif

Colors

Designer to choose colors to be used in the design.

Requirements
Must have
• A Black backside with the Hartuvo logo on it. The front side should be clean with only my contact details.
• But I'm also open for something really different or awesome!
Nice to have
• Remember that we are in the parts & repairing industry, So i'll be handing those business cards mainly to repair companies. Maybe you can do something with that thought :)

```html
<!DOCTYPE html>
<html lang="en">
<head>
<meta charset="utf-8">
<title>Hartuvo Business Card</title>
<link href="https://fonts.googleapis.com/css2?family=Exo+2:wght@400;600;700&family=Open+Sans:wght@700&display=swap" rel="stylesheet">
<style>
  :root {
    --orange: #f2711f;
    --orange-light: #f58a45;
    --white: #ffffff;
    --black: #050505;
    --backdrop: #e9e6e1;
  }
  html, body {
    margin: 0;
    padding: 0;
    overflow: hidden;
  }
  .canvas {
    width: 1200px;
    height: 950px;
    background: var(--backdrop);
    display: flex;
    align-items: center;
    justify-content: center;
    gap: 60px;
  }
  .card {
    width: 420px;
    height: 650px;
    position: relative;
    overflow: hidden;
    box-shadow: 0 12px 30px rgba(0,0,0,0.25);
  }
  .card--front {
    background: linear-gradient(160deg, var(--orange) 0%, var(--orange-light) 100%);
    color: var(--white);
  }
  .contact {
    position: absolute;
    top: 70px;
    left: 0;
    right: 0;
    text-align: center;
    font-family: "Exo 2", sans-serif;
  }
  .contact__name {
    margin: 0;
    font-size: 26px;
    font-weight: 700;
    letter-spacing: 1px;
  }
  .contact__divider {
    width: 34px;
    height: 1px;
    background: var(--white);
    margin: 16px auto 18px;
    border: 0;
  }
  .contact__list {
    list-style: none;
    margin: 0;
    padding: 0;
    font-size: 18px;
    line-height: 1.45;
    font-weight: 400;
  }
  .contact__label {
    font-weight: 700;
  }
  .front-graphic {
    position: absolute;
    left: 0;
    bottom: 0;
    width: 420px;
    height: 360px;
  }
  .card--back {
    background: var(--black);
  }
  .brand {
    position: absolute;
    top: 290px;
    left: 0;
    right: 0;
    display: flex;
    align-items: center;
    justify-content: center;
    gap: 16px;
  }
  .brand__dot {
    width: 46px;
    height: 46px;
    border-radius: 50%;
    background: var(--orange);
  }
  .brand__name {
    font-family: "Exo 2", sans-serif;
    font-weight: 600;
    font-size: 56px;
    color: var(--white);
    letter-spacing: 2px;
    line-height: 1;
  }
  .slogan {
    position: absolute;
    bottom: 70px;
    left: 0;
    right: 0;
    text-align: center;
    font-family: "Open Sans", sans-serif;
    font-weight: 700;
    font-size: 20px;
    color: var(--orange);
    margin: 0;
  }
</style>
</head>
<body>
<main class="canvas">
  <section class="card card--front" aria-label="Card front">
    <div class="contact">
      <h1 class="contact__name">Tobias Lindqvist</h1>
      <hr class="contact__divider">
      <ul class="contact__list">
        <li><span class="contact__label">Phone:</span> 0031687203316</li>
        <li><span class="contact__label">Email:</span> Tobias@hartuvo.nl</li>
        <li><span class="contact__label">Web:</span> www.hartuvo.nl</li>
      </ul>
    </div>
    <svg class="front-graphic" viewBox="0 0 420 360" role="img" aria-label="Large white wrench graphic across the lower card">
      <defs>
        <linearGradient id="graphicFill" x1="0" y1="0" x2="1" y2="1">
          <stop offset="0" stop-color="#ffffff" stop-opacity="0.95"/>
          <stop offset="1" stop-color="#fde3d2" stop-opacity="0.95"/>
        </linearGradient>
      </defs>
      <polygon points="0,120 420,40 420,200 0,360" fill="url(#graphicFill)"/>
    </svg>
  </section>

  <section class="card card--back" aria-label="Card back">
    <div class="brand">
      <span class="brand__dot"></span>
      <span class="brand__name">hartuvo</span>
    </div>
    <p class="slogan">Because Quality Matters</p>
  </section>
</main>
</body>
</html>
```